Sparrow Haulage needs a business card design.

Design a double-sided business card for new freight business. On the front, would like to see our logo along with the following info:

Martin Obuya
CEO/FOUNDER
555-206-7142
martinobuya@sparrow-haulage.example

On the reverse side, we would like to use the graphic image of our logo only without the Sparrow Haulage name.

```html
<!DOCTYPE html>
<html lang="en">
<head>
<meta charset="utf-8">
<title>Sparrow Haulage – Business Card</title>
<link rel="stylesheet" href="https://fonts.googleapis.com/css2?family=Arimo:wght@400;700&display=swap">
<style>
  :root {
    --stage: #2b2b2d;
    --navy: #0b0f6b;
    --navy-deep: #05054f;
    --navy-soft: #14189a;
    --red: #c0121c;
    --ink: #2a2a2a;
    --paper: #ffffff;
    --rule: #c9c9c9;
  }
  * { margin: 0; padding: 0; box-sizing: border-box; }
  html, body {
    width: 1200px; height: 900px; overflow: hidden;
    background: var(--stage);
    font-family: "Arimo", Arial, sans-serif;
  }
  .sheet {
    width: 1200px; height: 900px;
    display: flex; flex-direction: column; align-items: center;
    justify-content: center; gap: 40px;
  }
  .card {
    width: 700px; height: 400px; position: relative;
    box-shadow: 0 14px 30px rgba(0,0,0,.55);
  }

  /* Reverse side: symbol only */
  .card--back {
    background: var(--navy-deep);
    display: flex; align-items: center; justify-content: center;
  }
  .back-symbol {
    width: 120px; height: 120px;
    background: linear-gradient(160deg, var(--navy-deep), var(--navy-soft));
  }

  /* Front side */
  .card--front { background: var(--paper); }
  .brand {
    position: absolute; left: 52px; top: 196px;
    display: flex; align-items: center; gap: 14px;
  }
  .brand .mark-square { width: 40px; height: 40px; background: var(--navy); flex: none; }
  .brand-name {
    color: var(--navy); font-weight: 700; font-size: 21px;
    text-transform: uppercase; letter-spacing: 3px; line-height: 1.05;
  }
  .brand-name span { display: block; }
  .divider {
    position: absolute; left: 330px; top: 60px; width: 1px; height: 250px;
    background: linear-gradient(to bottom, transparent, var(--rule) 20%, var(--rule) 80%, transparent);
  }
  .details { position: absolute; left: 362px; top: 92px; }
  .person-name {
    font-weight: 700; font-size: 27px; letter-spacing: .5px;
    text-transform: uppercase; color: var(--navy); line-height: 1;
  }
  .person-name .surname { color: var(--red); }
  .person-role {
    font-size: 18px; color: var(--ink); margin-top: 4px; letter-spacing: .5px;
  }
  .contacts { list-style: none; margin-top: 30px; }
  .contacts li {
    display: flex; align-items: center; gap: 10px;
    font-size: 15px; color: var(--ink); line-height: 1; margin-bottom: 10px;
    white-space: nowrap;
  }
  .contacts svg { width: 15px; height: 15px; flex: none; }
  .icon-fill { fill: var(--red); }
  .icon-line { fill: none; stroke: var(--red); stroke-width: 2; }
  .web .domain { color: var(--navy); }
  .web .domain-tail { color: var(--red); }
</style>
</head>
<body>
<main class="sheet">
  <section class="card card--back" aria-label="Card reverse">
    <div class="back-symbol" role="img" aria-label="Company symbol"></div>
  </section>

  <section class="card card--front" aria-label="Card front">
    <div class="brand">
      <span class="mark-square"></span>
      <span class="brand-name"><span>Sparrow</span><span>Haulage</span></span>
    </div>
    <div class="divider"></div>
    <div class="details">
      <h1 class="person-name">Martin <span class="surname">Obuya</span></h1>
      <p class="person-role">CEO/FOUNDER</p>
      <ul class="contacts">
        <li>
          <svg viewBox="0 0 24 24" aria-hidden="true"><path class="icon-fill" d="M6.6 10.8a15 15 0 0 0 6.6 6.6l2.2-2.2a1 1 0 0 1 1-.25c1.1.37 2.3.57 3.6.57a1 1 0 0 1 1 1V20a1 1 0 0 1-1 1C10.6 21 3 13.4 3 4a1 1 0 0 1 1-1h3.5a1 1 0 0 1 1 1c0 1.25.2 2.45.57 3.57a1 1 0 0 1-.25 1z"/></svg>
          555-206-7142
        </li>
        <li>
          <svg viewBox="0 0 24 24" aria-hidden="true"><path class="icon-fill" d="M2 5h20v14H2z"/><path d="M2 6l10 7 10-7" fill="none" stroke="#fff" stroke-width="1.6"/></svg>
          martinobuya@sparrow-haulage.example
        </li>
        <li class="web">
          <svg viewBox="0 0 24 24" aria-hidden="true"><circle class="icon-line" cx="12" cy="12" r="9"/><ellipse class="icon-line" cx="12" cy="12" rx="4" ry="9"/><path class="icon-line" d="M3 12h18M5 7h14M5 17h14"/></svg>
          <span>www.<span class="domain">sparrow</span><span class="domain-tail">-haulage</span>.example</span>
        </li>
      </ul>
    </div>
  </section>
</main>
</body>
</html>
```